Direct to Consumer extended service contract business with a new disruptive business model needs a

We need a customized wordpress design for a company called 'Bright Harbor Assurance'.
We provide an innovative and unique service contract protection program direct to consumers. This program provides monthly coverage for all electronics purchased in the last 4 years and all electronics the consumer purchases in the future for a low monthly fee. The overall design should communicate a sense of legitimacy, ethics, and superior customer service and support (in an industry that has a huge PR issue to overcome).
Electronics is the first product group, other product groups with different price points to launch in the future..

Target Market(s)

All purchasers of electronic goods...all demographics

Industry/Entity Type

Electronics

Font styles to use
Sans Serif

Requirements
Must have
• Customer Testimonials
Industry News
Customer ratings
Blog posts
Call to action messaging
Like the functional elements and design of quillmesa.example (need to be better)
Nice to have
• Like to see video testimonials
Social network "whats trending related to electronics or service contract industry"
Easy way to register products for warranty

```html
<!DOCTYPE html>
<html lang="en">
<head>
<meta charset="utf-8">
<title>Bright Harbor Assurance</title>
<link href="https://fonts.googleapis.com/css2?family=Open+Sans:wght@400;600;700;800&display=swap" rel="stylesheet">
<style>
:root{
  --green:#1f9a4a;
  --green-dark:#14552d;
  --navy:#1b3f7a;
  --navy-tag:#1d4f86;
  --slate:#5b6f7a;
  --ink:#222;
  --text:#555;
  --muted:#888;
  --rule:#d9d9d9;
  --nav-active:#6b6b6b;
  --field:#e9e9e9;
  --star:#e0473a;
  --star-gold:#e8a13a;
  --link:#2e4fa0;
  --play:#c0151b;
}
*{box-sizing:border-box;margin:0;padding:0}
html,body{width:1200px;height:2532px;overflow:hidden;background:#fff}
body{position:relative;font-family:"Open Sans",Arial,sans-serif;color:var(--ink)}
.abs{position:absolute}

/* header */
.brand{left:101px;top:24px;color:var(--green);font-weight:800;font-size:27px;letter-spacing:1px;display:flex;align-items:center;gap:10px}
.brand-mark{width:16px;height:16px;background:var(--green)}
.support{left:572px;top:30px;display:flex;align-items:center;gap:12px;font-size:17px;color:var(--muted)}
.support-icon{width:34px;height:34px;border-radius:50%;background:#9a9a9a}
.btn-head{top:32px;height:32px;color:#fff;font-size:14px;display:flex;align-items:center;justify-content:center}
.btn-signup{left:925px;width:81px;background:#555}
.btn-login{left:1017px;width:83px;background:var(--green)}

/* nav */
.nav{left:0;top:96px;width:1200px;height:46px;background:var(--green)}
.nav a{position:absolute;top:0;height:46px;line-height:46px;color:#fff;font-size:15px;text-decoration:none}
.nav a.active{background:var(--nav-active);width:117px;left:101px;text-align:center}

/* hero */
.hero{left:0;top:142px;width:1200px;height:510px;background:linear-gradient(100deg,#4a5560 0%,#7a6e5a 35%,#b59a7a 60%,#6a7480 100%)}
.hero-content{left:0;top:216px;width:1200px;text-align:center;color:#fff}
.hero-content h1{font-size:34px;font-weight:700;line-height:41px}
.hero-sub{margin-top:28px;font-size:21px;line-height:27px}
.hero-sub .hl{color:var(--green);font-weight:700}
.hero-sub strong{font-weight:700}
.play{left:565px;top:399px}
.hero-cta{left:0;top:486px;width:1200px;text-align:center;color:#fff;font-weight:800;font-size:21px}
.hero-btn{left:505px;top:528px;width:201px;height:49px;background:var(--green);color:#fff;font-size:25px;display:flex;align-items:center;justify-content:center;box-shadow:0 4px 0 var(--green-dark)}

/* who we are */
.section-title{width:1200px;left:0;text-align:center;font-size:31px;color:#444;font-weight:400}
.who-text{left:140px;top:752px;width:920px;text-align:center;font-size:14.5px;line-height:24px;color:var(--muted);letter-spacing:1px}
.ratings-title{left:0;top:853px;width:1200px;text-align:center;font-size:20px;color:#333;font-weight:400}
.rating{top:905px;text-align:center;width:190px}
.rating .name{font-size:14px;font-weight:700;margin-top:2px}
.rating .meta{font-size:11px;color:#555}
.badge{left:797px;top:912px;display:flex;gap:8px}
.badge span{display:block;background:var(--navy-tag);width:94px;height:36px;border-radius:3px}
.badge span+span{background:#fff;border:2px solid var(--navy-tag);width:42px}
.badge-meta{left:745px;top:962px;width:240px;text-align:center;font-size:11px;color:#555;white-space:nowrap}
.read-more{left:0;top:1012px;width:1200px;text-align:center;font-size:13px;color:#333}

/* blog / news */
.blog{left:101px;top:1080px;width:999px;height:324px;border:1.5px solid #333;border-bottom:none}
.news{left:101px;top:1404px;width:999px;height:325px;background:#000}
.block-title{position:absolute;left:0;width:100%;text-align:center;font-size:31px;font-weight:400}
.post{position:absolute;width:440px;height:136px}
.post-img{position:absolute;left:0;top:0;width:131px;height:136px}
.post-body{position:absolute;left:150px;top:0;width:282px}
.post h3{font-size:13.5px;font-weight:700;line-height:18px}
.post p{font-size:12px;line-height:15px;margin-top:10px;color:#444}
.news .post h3{color:#fff}
.news .post p{color:#ccc}
.tags{position:absolute;left:150px;top:120px;display:flex;gap:6px;font-size:9.5px;font-weight:700;color:#fff}
.tags span{height:16px;line-height:16px;padding:0 8px;display:block}
.tag-date{background:var(--navy-tag);width:71px}
.tag-count{background:var(--slate);width:34px;text-align:center}
.tag-more{background:#444}

/* testimonials */
.testi-title{left:101px;top:1768px;font-size:30px;color:#444;font-weight:400}
.arrow{top:1776px;width:23px;height:23px;border-radius:50%}
.testi{position:absolute;top:1847px;width:320px;height:90px}
.testi-img{position:absolute;left:0;top:0;width:110px;height:90px}
.testi-play{position:absolute;left:42px;top:32px;width:26px;height:26px;border-radius:50%;background:var(--play)}
.testi-play::after{content:"";position:absolute;left:10px;top:7px;border-left:9px solid #fff;border-top:6px solid transparent;border-bottom:6px solid transparent}
.testi-body{position:absolute;left:128px;top:0;width:195px}
.testi-body p{font-size:12px;line-height:17px;color:#333;text-align:justify}
.quote{color:#ccc;font-weight:800;font-size:34px;line-height:20px;float:left;margin-right:6px}
.testi-name{font-size:13px;margin-top:8px;color:#333}
.testi-role{font-size:10px;color:#999}
.testi-role a{color:var(--link);text-decoration:none}

/* cta */
.cta{left:101px;top:2005px;width:999px;height:105px;background:var(--green)}
.cta-text{position:absolute;left:137px;top:32px;color:#fff;font-size:30px}
.cta-btn{position:absolute;left:594px;top:31px;width:254px;height:47px;background:var(--green-dark);color:#fff;font-size:18px;display:flex;align-items:center;justify-content:center;letter-spacing:.5px}

/* footer */
.footer-rule{left:0;top:2182px;width:1200px;height:1px;background:var(--rule)}
.col-title{top:2230px;font-size:14px;font-weight:700;color:#222}
.vsep{top:2240px;width:1px;height:195px;background:var(--rule)}
.links{left:101px;top:2268px;list-style:none;font-size:14px;color:#555;line-height:21.5px}
.links li::before{content:"›";margin-right:10px;color:#555}
.field{left:331px;width:186px;height:32px;background:var(--field);font-size:13px;color:#666;padding-left:14px;line-height:32px}
.subscribe{left:331px;top:2383px;width:186px;height:33px;background:var(--green);color:#fff;font-size:13px;text-align:center;line-height:33px;box-shadow:0 3px 0 var(--green-dark)}
.feed-login{left:778px;top:2224px;width:56px;height:25px;background:#6a80b3;color:#fff;font-size:14px;font-weight:600;text-align:center;line-height:25px}
.feed{left:584px;width:270px;height:64px;border-top:1px solid var(--rule);padding-top:10px}
.feed-img{position:absolute;left:0;top:10px;width:56px;height:56px}
.feed-body{position:absolute;left:73px;top:8px;width:200px;font-size:11px;line-height:13px;color:#333}
.feed-body b{color:var(--link);font-weight:400;display:block;margin-bottom:1px;font-size:12px}
.feed-body small{color:#777;font-size:10px}
.social{left:964px;width:30px;height:30px;border-radius:2px}
.bottom{left:0;top:2470px;width:1200px;height:62px;background:var(--navy);color:#fff;font-size:13px;text-align:center;line-height:62px}
</style>
</head>
<body>

<header>
  <div class="abs brand"><span class="brand-mark"></span>Bright Harbor Assurance</div>
  <div class="abs support"><span class="support-icon"></span><span>Support &nbsp;-&nbsp; 855-500-0199</span></div>
  <div class="abs btn-head btn-signup">SIGN UP</div>
  <div class="abs btn-head btn-login">LOGIN</div>
</header>

<nav class="abs nav">
  <a class="active" href="#">Home</a>
  <a style="left:258px" href="#">Plans</a>
  <a style="left:372px" href="#">Benefits</a>
  <a style="left:503px" href="#">FAQs</a>
  <a style="left:618px" href="#">Testimonias</a>
  <a style="left:773px" href="#">News</a>
  <a style="left:885px" href="#">Blog</a>
  <a style="left:992px" href="#">About Us</a>
</nav>

<section class="abs hero" role="img" aria-label="Blurred photo of shoppers at an electronics store counter"></section>
<div class="abs hero-content">
  <h1>The Days of Buying Expensive in-Store<br>Service Plans are Over!</h1>
  <p class="hero-sub">Dont Buy anymore <span class="hl">in-store</span> service plans.<br><strong>BRIGHT HARBOR ASSURANCE</strong> is the solution</p>
</div>
<svg class="abs play" width="70" height="70" viewBox="0 0 70 70" aria-hidden="true">
  <circle cx="35" cy="35" r="31" fill="none" stroke="#fff" stroke-width="4"/>
  <polygon points="28,21 50,35 28,49" fill="#fff"/>
</svg>
<div class="abs hero-cta">GET YOUR BRIGHT HARBOR ASSURANCE TODAY!</div>
<div class="abs hero-btn">Sign Up</div>

<section>
  <h2 class="abs section-title" style="top:690px">Who We Are</h2>
  <p class="abs who-text">Sed ut perspiciatis unde omnis iste natus error sit voluptatem accusantium doloremque totam rem aperiam, eaque ipsa quae ab illo inventore veritatis et quasi architecto beat dicta sunt explicabo. Nemo enim ipsam voluptatem quia. sit amet turpis ut purus pellentesque ullamcorper sed ut nisl.</p>
  <h3 class="abs ratings-title">Our Customer Ratings</h3>

  <div class="abs rating" style="left:212px">
    <svg width="140" height="28" viewBox="0 0 140 28" aria-hidden="true"><g fill="var(--star)">
      <polygon points="14,1 17.5,10 27,10 19.5,16 22,26 14,20 6,26 8.5,16 1,10 10.5,10"/>
      <polygon transform="translate(27 0)" points="14,1 17.5,10 27,10 19.5,16 22,26 14,20 6,26 8.5,16 1,10 10.5,10"/>
      <polygon transform="translate(54 0)" points="14,1 17.5,10 27,10 19.5,16 22,26 14,20 6,26 8.5,16 1,10 10.5,10"/>
      <polygon transform="translate(81 0)" points="14,1 17.5,10 27,10 19.5,16 22,26 14,20 6,26 8.5,16 1,10 10.5,10"/>
      <polygon transform="translate(108 0)" points="14,1 17.5,10 27,10 19.5,16 22,26 14,20 6,26 8.5,16 1,10 10.5,10" fill="#e6b2ad"/></g></svg>
    <div class="name">Orchard App Store</div>
    <div class="meta"><b>4.5</b> average on <b>7000+</b> reviews</div>
  </div>
  <div class="abs rating" style="left:400px">
    <svg width="140" height="28" viewBox="0 0 140 28" aria-hidden="true"><g fill="var(--star-gold)">
      <polygon points="14,1 17.5,10 27,10 19.5,16 22,26 14,20 6,26 8.5,16 1,10 10.5,10"/>
      <polygon transform="translate(27 0)" points="14,1 17.5,10 27,10 19.5,16 22,26 14,20 6,26 8.5,16 1,10 10.5,10"/>
      <polygon transform="translate(54 0)" points="14,1 17.5,10 27,10 19.5,16 22,26 14,20 6,26 8.5,16 1,10 10.5,10"/>
      <polygon transform="translate(81 0)" points="14,1 17.5,10 27,10 19.5,16 22,26 14,20 6,26 8.5,16 1,10 10.5,10"/>
      <polygon transform="translate(108 0)" points="14,1 17.5,10 27,10 19.5,16 22,26 14,20 6,26 8.5,16 1,10 10.5,10" fill="#f0cf96"/></g></svg>
    <div class="name">Riverway</div>
    <div class="meta"><b>4.7</b> average on <b>35,000+</b> reviews</div>
  </div>
  <div class="abs rating" style="left:588px">
    <svg width="140" height="28" viewBox="0 0 140 28" aria-hidden="true"><g fill="var(--star)">
      <polygon points="14,1 17.5,10 27,10 19.5,16 22,26 14,20 6,26 8.5,16 1,10 10.5,10"/>
      <polygon transform="translate(27 0)" points="14,1 17.5,10 27,10 19.5,16 22,26 14,20 6,26 8.5,16 1,10 10.5,10"/>
      <polygon transform="translate(54 0)" points="14,1 17.5,10 27,10 19.5,16 22,26 14,20 6,26 8.5,16 1,10 10.5,10"/>
      <polygon transform="translate(81 0)" points="14,1 17.5,10 27,10 19.5,16 22,26 14,20 6,26 8.5,16 1,10 10.5,10"/>
      <polygon transform="translate(108 0)" points="14,1 17.5,10 27,10 19.5,16 22,26 14,20 6,26 8.5,16 1,10 10.5,10"/></g></svg>
    <div class="name">Searchly</div>
    <div class="meta"><b>4.9</b> average on <b>600+</b> reviews</div>
  </div>
  <div class="abs badge" role="img" aria-label="Accreditation badge"><span></span><span></span></div>
  <div class="abs badge-meta">Trust Bureau Accredited with an <b>A+ Rating</b></div>
  <div class="abs read-more">READ MORE</div>
</section>

<section class="abs blog">
  <h2 class="block-title" style="top:30px;color:#444">Latest Blog</h2>
  <article class="post" style="left:35px;top:121px">
    <div class="post-img" role="img" aria-label="Photo of a technician with tools" style="background:linear-gradient(160deg,#c9b89c,#3d4e72)"></div>
    <div class="post-body">
      <h3>Fernwick Financial Group Participating in the 2014 Harborview Golf Tournament</h3>
      <p>mollis varius dolor id, varius molestie urna. Cras id tellus nisl. Fusce purus ante, elementum id metus eget, congue pharetra dolor. Sed non mollis quam. Nulla non eros diam.</p>
    </div>
    <div class="tags"><span class="tag-date">05 june 15</span><span class="tag-count">12</span><span class="tag-more">Read More</span></div>
  </article>
  <article class="post" style="left:531px;top:121px">
    <div class="post-img" role="img" aria-label="Photo of a circuit board" style="background:linear-gradient(150deg,#a8c2cf,#2d4f63)"></div>
    <div class="post-body">
      <h3>New Product: Foreign Exchange</h3>
      <p>mollis varius dolor id, varius molestie urna. Cras id tellus nisl. Fusce purus ante, elementum id metus eget, congue pharetra dolor. Sed non mollis quam. Nulla non eros diam. Proin ultricies, felis eget sceler-isque</p>
    </div>
    <div class="tags"><span class="tag-date">05 june 15</span><span class="tag-count">12</span><span class="tag-more">Read More</span></div>
  </article>
</section>

<section class="abs news">
  <h2 class="block-title" style="top:24px;color:#fff">Industry News</h2>
  <article class="post" style="left:35px;top:122px">
    <div class="post-img" role="img" aria-label="Photo of a shopper in an electronics aisle" style="background:linear-gradient(160deg,#6e8fc4,#d8dde6)"></div>
    <div class="post-body">
      <h3>Fernwick Financial Group Participating in the 2014 Harborview Golf Tournament</h3>
      <p>mollis varius dolor id, varius molestie urna. Cras id tellus nisl. Fusce purus ante, elementum id metus eget, congue pharetra dolor. Sed non mollis quam. Nulla non eros diam.</p>
    </div>
    <div class="tags"><span class="tag-date">05 june 15</span><span class="tag-count">12</span><span class="tag-more">Read More</span></div>
  </article>
  <article class="post" style="left:531px;top:122px">
    <div class="post-img" role="img" aria-label="Photo of an industrial facility" style="background:linear-gradient(150deg,#8fb2b8,#2f5560)"></div>
    <div class="post-body">
      <h3>New Product: Foreign Exchange</h3>
      <p>mollis varius dolor id, varius molestie urna. Cras id tellus nisl. Fusce purus ante, elementum id metus eget, congue pharetra dolor. Sed non mollis quam. Nulla non eros diam. Proin ultricies, felis eget sceler-isque</p>
    </div>
    <div class="tags"><span class="tag-date">05 june 15</span><span class="tag-count">12</span><span class="tag-more">Read More</span></div>
  </article>
</section>

<section>
  <h2 class="abs testi-title">Customer Testimonials</h2>
  <svg class="abs arrow" style="left:1040px" viewBox="0 0 23 23" aria-hidden="true"><circle cx="11.5" cy="11.5" r="11.5" fill="#ccc"/><path d="M13.5 6.5 8.5 11.5 13.5 16.5" stroke="#fff" stroke-width="2.5" fill="none"/></svg>
  <svg class="abs arrow" style="left:1071px" viewBox="0 0 23 23" aria-hidden="true"><circle cx="11.5" cy="11.5" r="11.5" fill="var(--green)"/><path d="M9.5 6.5 14.5 11.5 9.5 16.5" stroke="#fff" stroke-width="2.5" fill="none"/></svg>

  <div class="testi" style="left:103px">
    <div class="testi-img" role="img" aria-label="Video testimonial thumbnail" style="background:linear-gradient(135deg,#8a96a6,#3e4652)"></div>
    <div class="testi-play"></div>
    <div class="testi-body"><p><span class="quote">“</span>Pellentesque et pulvinar enim. Quisque at tempor ligula. Donec ut purus sed tortor malesuada.</p>
      <div class="testi-name">Dana Marlow</div><div class="testi-role">Art Director / <a href="#">lorem ipsum</a></div></div>
  </div>
  <div class="testi" style="left:442px">
    <div class="testi-img" role="img" aria-label="Video testimonial thumbnail" style="background:linear-gradient(135deg,#b9b9b9,#5e5a57)"></div>
    <div class="testi-play"></div>
    <div class="testi-body"><p><span class="quote">“</span>Pellentesque et pulvinar enim. Quisque at tempor ligula. Donec ut purus sed tortor malesuada.</p>
      <div class="testi-name">Dana Marlow</div><div class="testi-role">Art Director / <a href="#">lorem ipsum</a></div></div>
  </div>
  <div class="testi" style="left:782px">
    <div class="testi-img" role="img" aria-label="Video testimonial thumbnail" style="background:linear-gradient(135deg,#d8cfc2,#8a7a62)"></div>
    <div class="testi-play"></div>
    <div class="testi-body"><p><span class="quote">“</span>Pellentesque et pulvinar enim. Quisque at tempor ligula. Donec ut purus sed tortor malesuada.</p>
      <div class="testi-name">Dana Marlow</div><div class="testi-role">Art Director / <a href="#">lorem ipsum</a></div></div>
  </div>
</section>

<section class="abs cta">
  <div class="cta-text">Contact With Our Experts Now</div>
  <div class="cta-btn">CALL TO ACTION</div>
</section>

<footer>
  <div class="abs footer-rule"></div>
  <div class="abs col-title" style="left:101px">LINKS</div>
  <ul class="abs links"><li>Home</li><li>About Us</li><li>Contact Us</li><li>FAQ</li><li>Privacy Policy</li></ul>
  <div class="abs vsep" style="left:287px"></div>

  <div class="abs col-title" style="left:329px">NEWSLETTER</div>
  <div class="abs field" style="top:2274px">Name</div>
  <div class="abs field" style="top:2318px">Email id</div>
  <div class="abs subscribe">Subscrib Now</div>
  <div class="abs vsep" style="left:554px"></div>

  <div class="abs col-title" style="left:582px;top:2226px;font-weight:600">SOCIAL FEED</div>
  <div class="abs feed-login">Login</div>
  <div class="abs feed" style="top:2276px">
    <div class="feed-img" role="img" aria-label="Video thumbnail" style="background:linear-gradient(135deg,#c89a7a,#5a3f30)"></div>
    <div class="feed-body"><b>Fresh Video Widget Set</b>Lorem ipsum dolor sit amet, con adipiscing elit. Praesent viverra ult ultrices.<br><small>6 people recommend this.</small></div>
  </div>
  <div class="abs feed" style="top:2366px;border-top:none">
    <div class="feed-img" role="img" aria-label="Video thumbnail" style="background:linear-gradient(135deg,#9cc79a,#3f6a4a)"></div>
    <div class="feed-body"><b>Fresh Video Widget Set</b>Lorem ipsum dolor sit amet, con adipiscing elit. Praesent viverra ult ultrices.<br><small>6 people recommend this.</small></div>
  </div>
  <div class="abs vsep" style="left:906px"></div>

  <div class="abs col-title" style="left:962px;top:2224px">STAYING IN TOUCH</div>
  <div class="abs social" style="top:2267px;background:#3b5998"></div>
  <div class="abs social" style="top:2306px;background:#ccc"></div>
  <div class="abs social" style="top:2346px;background:#ccc"></div>

  <div class="abs bottom">Copyright © yourwebsite &nbsp;|&nbsp; Terms &amp; Conditions &nbsp;|&nbsp; Privacy Policy &nbsp;|&nbsp; 14 Larch Avenue Northfield 2000</div>
</footer>

</body>
</html>
```